Candle Rental Business seeks new website design

We need a new website design for a Candle hire business. The business rents out pillar candles for events such as weddings and corporate events. Our main target market is weddings. The business name is Hire a Lantern. The business name does not have a logo design.

We would like a website that is light in colours and creates a warm atmosphere. The design needs to be elegant and upmarket. There are different size candles that we hire out, ranging from 10cm diameter to 20cm diameter, flat, tall etc. All our candles are white in colour. Its just the size that differs.

We would also like to include a section for hiring out decor such as glassvases, candlebras, overlays and chairs sachets, chair covers. However, this is not the businesses main focus but an additional offering to customers.

Target Market(s)

Wedding venues and brides. Corporate events. School dances.

Industry/Entity Type

Hospitality

Logo Text

Hire a Lantern

Number of Pages Required

1 page

Font styles to use
Sans Serif
Script

Requirements
Must have
• Pictures of pillar candles. Plain white candles. The website must centre around candles.
Nice to have
• Different examples of candle centrepieces
Should not have
• Pictures must not be of brides. Pictures of surrounding is perferable.

```html
<!DOCTYPE html>
<html lang="en">
<head>
<meta charset="utf-8">
<title>Hire a Lantern – Candle Hire</title>
<link rel="stylesheet" href="https://fonts.googleapis.com/css2?family=Dancing+Script:wght@700&family=Lato:ital,wght@0,400;0,700;1,400&family=Roboto:wght@400;500&display=swap">
<style>
:root{
  --green:#4a7520;
  --ink:#1d1d1d;
  --text:#333;
  --rule:#c9c9c9;
  --pale-green:#f2f7ee;
  --pale-grey:#f3f3f3;
  --footer-top:#2a2a2a;
  --footer-bottom:#050505;
  --bar:#1b1b1b;
  --white:#fff;
}
*{box-sizing:border-box;margin:0;padding:0}
html,body{width:1200px;height:2532px;overflow:hidden}
body{font-family:"Lato",sans-serif;color:var(--text);background:var(--white);position:relative}

/* header */
.site-header{position:absolute;top:0;left:0;width:1200px;height:138px;background:linear-gradient(#f4f4f4,#fff)}
.brand{position:absolute;left:62px;top:96px;display:flex;align-items:center;gap:10px;font-family:"Dancing Script",cursive;font-weight:700;font-size:34px;color:var(--ink);line-height:1}
.brand-dot{width:14px;height:14px;border-radius:50%;background:var(--green)}
.contact-bar{position:absolute;right:66px;top:26px;display:flex;align-items:center;font-family:"Roboto",sans-serif;font-size:17px;color:var(--ink)}
.contact-bar span{display:flex;align-items:center;gap:6px}
.contact-bar .divider{width:1px;height:30px;background:#ccc;margin:0 26px}
.main-nav{position:absolute;right:40px;top:95px;display:flex;font-family:"Roboto",sans-serif;font-size:15px;color:var(--ink)}
.main-nav a{color:inherit;text-decoration:none;padding:0 26px;position:relative;height:43px}
.main-nav a.active{color:var(--green)}
.main-nav a.active::after{content:"";position:absolute;left:26px;right:26px;bottom:-8px;height:2px;background:var(--green)}

/* hero */
.hero{position:absolute;top:138px;left:0;width:1200px;height:462px;background:radial-gradient(ellipse at 50% 60%,#f2ead0 0%,#d8cfa8 12%,#8a7a5a 38%,#4a3a2e 70%,#2d2420 100%);display:flex;align-items:center;justify-content:center}
.hero h1{font-family:"Dancing Script",cursive;font-weight:700;font-size:47px;color:var(--white);text-shadow:0 2px 6px rgba(0,0,0,.5);margin-top:-6px}

/* section titles */
.section-title{text-align:center;font-family:"Dancing Script",cursive;font-weight:700;font-size:38px;color:var(--ink)}
.section-title em{font-style:normal;color:var(--green)}
.title-rule{display:block;margin:6px auto 0}

.about{position:absolute;top:600px;left:0;width:1200px;height:235px;padding-top:40px}
.about p{width:1000px;margin:20px auto 0;text-align:center;font-size:14.5px;line-height:26px;color:var(--ink)}

/* services */
.services{position:absolute;top:835px;left:0;width:1200px;height:535px;background:var(--pale-green);padding-top:42px}
.service-cards{position:absolute;top:150px;left:60px;display:flex;gap:34px}
.card{width:337px;height:335px;background:var(--white);box-shadow:0 1px 4px rgba(0,0,0,.12);position:relative}
.card h3{height:58px;background:var(--green);color:var(--white);font-family:"Roboto",sans-serif;font-weight:400;font-size:23px;padding:15px 14px}
.card .photo{width:322px;height:137px;margin:10px auto 0}
.card p{padding:16px 24px 0 9px;font-size:14.5px;line-height:23.5px;color:var(--ink)}
.card .more{position:absolute;right:0;bottom:0;width:38px;height:38px;background:#3a3a3a;display:flex;align-items:center;justify-content:center}

/* products */
.products{position:absolute;top:1370px;left:0;width:1200px;height:533px;padding-top:42px}
.tile{position:absolute}
.tile-overlay{position:absolute;inset:0;background:rgba(0,0,0,.4);display:flex;flex-direction:column;align-items:center;justify-content:center;gap:18px;color:var(--white);font-family:"Roboto",sans-serif;font-weight:500;font-size:15px}
.zoom{width:40px;height:40px;border-radius:50%;background:var(--white);display:flex;align-items:center;justify-content:center}

/* testimonial */
.testimonial{position:absolute;top:1903px;left:0;width:1200px;height:319px;background:var(--pale-grey);padding-top:42px}
.avatar{position:absolute;left:62px;top:134px;width:104px;height:104px;border-radius:50%;border:3px solid var(--green);background:radial-gradient(circle at 50% 40%,#e9dccf,#c9b6a3)}
.quote{position:absolute;left:192px;top:140px;width:880px;font-style:italic;font-size:14.5px;line-height:24px;color:#444}
.quote .mark{font-size:40px;color:#bbb;line-height:0;vertical-align:-10px;font-family:Georgia,serif}
.quote-rule{position:absolute;left:192px;top:220px;width:780px;height:1px;background:#ddd}
.author{position:absolute;left:192px;top:228px;font-weight:700;font-size:14px;color:var(--ink)}
.dots{position:absolute;left:88px;top:262px;display:flex;gap:6px}
.dots i{width:9px;height:9px;border-radius:50%;background:#ccc;display:block}
.dots i.on{background:var(--white);border:2px solid var(--green)}

/* footer */
.site-footer{position:absolute;top:2222px;left:0;width:1200px;height:262px;background:linear-gradient(var(--footer-top),var(--footer-bottom));border-top:2px solid var(--green);color:var(--white)}
.f-col{position:absolute;top:26px;height:220px}
.f-col+.f-col{border-left:1px solid #3a3a3a}
.f-col h4{font-family:"Roboto",sans-serif;font-weight:400;font-size:18px;padding-bottom:10px;position:relative}
.f-col h4::after{content:"";position:absolute;left:0;bottom:0;width:50px;height:1px;background:#777}
.quick-links{list-style:none;margin-top:14px;font-size:12.5px;line-height:23.5px}
.quick-links li::before{content:"\25B8";font-size:10px;margin-right:6px}
.contact-row{display:flex;gap:14px;font-size:12.5px;line-height:21px;margin-top:14px}
.contact-row.big{font-family:"Roboto",sans-serif;font-weight:500;font-size:17px}
.inquiry input,.inquiry textarea{display:block;width:222px;border:0;background:var(--white);font:12px "Lato",sans-serif;color:#888;padding:4px 6px;margin-top:8px}
.inquiry input{height:26px}
.inquiry textarea{height:64px;resize:none}
.inquiry button{margin-top:8px;background:var(--green);color:var(--white);border:0;font:700 12px "Lato",sans-serif;padding:6px 13px}
.footer-brand{position:absolute;left:905px;top:158px;width:250px;display:flex;align-items:center;justify-content:center;gap:10px;font-family:"Dancing Script",cursive;font-weight:700;font-size:30px;color:var(--white)}
.footer-brand .brand-dot{background:#aaa}

.bottom-bar{position:absolute;top:2484px;left:0;width:1200px;height:48px;background:var(--bar);color:#ddd;font-size:12.5px}
.copyright{position:absolute;left:62px;top:16px}
.social{position:absolute;right:62px;top:8px;display:flex;align-items:center;gap:8px;font-weight:700;color:var(--white)}
.social span{margin-right:24px}
.social i{width:30px;height:30px;border-radius:50%;background:var(--white);display:block}
</style>
</head>
<body>

<header class="site-header">
  <div class="brand"><span class="brand-dot"></span>Hire a Lantern</div>
  <div class="contact-bar">
    <span><svg width="15" height="15" viewBox="0 0 24 24"><path fill="#222" d="M6.6 10.8a15 15 0 0 0 6.6 6.6l2.2-2.2c.3-.3.7-.4 1-.2 1.1.4 2.3.6 3.6.6.6 0 1 .4 1 1V20c0 .6-.4 1-1 1A17 17 0 0 1 3 4c0-.6.4-1 1-1h3.5c.6 0 1 .4 1 1 0 1.3.2 2.5.6 3.6.1.3 0 .7-.2 1z"/></svg>: 0198-765-432</span>
    <span class="divider"></span>
    <span><svg width="17" height="13" viewBox="0 0 24 18"><path fill="#222" d="M0 0h24v2L12 10 0 2zM0 4l12 8 12-8v14H0z"/></svg>: info@hirealantern.com</span>
  </div>
  <nav class="main-nav">
    <a class="active">Home</a><a>About Us</a><a>Weddings</a><a>Corporate events</a><a>For Hire</a><a>Contact</a>
  </nav>
</header>

<section class="hero" role="img" aria-label="Wedding table centrepiece with a white pillar candle, cream roses and wine glasses">
  <h1>Meaningful gift at a friendly price point</h1>
</section>

<section class="about">
  <h2 class="section-title">About <em>Hire a lantern</em></h2>
  <svg class="title-rule" width="180" height="12" viewBox="0 0 180 12"><rect x="0" y="2" width="70" height="2" fill="var(--rule)"/><rect x="0" y="7" width="70" height="2" fill="var(--rule)"/><circle cx="90" cy="6" r="4" fill="var(--green)"/><rect x="110" y="2" width="70" height="2" fill="var(--rule)"/><rect x="110" y="7" width="70" height="2" fill="var(--rule)"/></svg>
  <p>We are a family owned and operated company and began making decorative candles for all occasions.&nbsp; All of our candles are individually hand made in our candle studio, situated in Riverton, outside Hillcrest.&nbsp; Our wax is local and of a very high quality, and dripless! Our wax is also made with a high melting point, which means it will not melt or bend in hot temperatures. Our Products</p>
</section>

<section class="services">
  <h2 class="section-title">Our <em>Services</em></h2>
  <svg class="title-rule" width="180" height="12" viewBox="0 0 180 12"><rect x="0" y="2" width="70" height="2" fill="var(--rule)"/><rect x="0" y="7" width="70" height="2" fill="var(--rule)"/><circle cx="90" cy="6" r="4" fill="var(--green)"/><rect x="110" y="2" width="70" height="2" fill="var(--rule)"/><rect x="110" y="7" width="70" height="2" fill="var(--rule)"/></svg>
  <div class="service-cards">
    <article class="card">
      <h3>Hire Candles</h3>
      <div class="photo" role="img" aria-label="Lit white pillar candles on a long dinner table" style="background:linear-gradient(120deg,#3a3328,#8d7d60 45%,#d9ccb0 60%,#4a3f30)"></div>
      <p>Do you love using candles for your events but tired of sorting old used candles or buying expensive candles.</p>
      <span class="more"><svg width="12" height="16" viewBox="0 0 12 16"><path d="M3 2l6 6-6 6" stroke="#fff" stroke-width="3" fill="none"/></svg></span>
    </article>
    <article class="card">
      <h3>Personalized Candles</h3>
      <div class="photo" role="img" aria-label="Three white pillar candles with a ribbon flower" style="background:linear-gradient(90deg,#1f2a16,#3e4d2a 30%,#d8d4cc 50%,#3e4d2a 70%,#1f2a16)"></div>
      <p>Hire a Lantern provides the opportunity to give a thoughtful, meaningful gift at a friendly price point. This unique gift.</p>
      <span class="more"><svg width="12" height="16" viewBox="0 0 12 16"><path d="M3 2l6 6-6 6" stroke="#fff" stroke-width="3" fill="none"/></svg></span>
    </article>
    <article class="card">
      <h3>Decor Hire</h3>
      <div class="photo" role="img" aria-label="Reception hall lit in pink with candelabras on tables" style="background:linear-gradient(180deg,#c23fc0,#8a2a94 55%,#2c1430)"></div>
      <p>We hire a selection of overlays, chair sachets and chair covers as well as glassware and candelabras to compliment.</p>
      <span class="more"><svg width="12" height="16" viewBox="0 0 12 16"><path d="M3 2l6 6-6 6" stroke="#fff" stroke-width="3" fill="none"/></svg></span>
    </article>
  </div>
</section>

<section class="products">
  <h2 class="section-title">Our <em>Products</em></h2>
  <svg class="title-rule" width="180" height="12" viewBox="0 0 180 12"><rect x="0" y="2" width="70" height="2" fill="var(--rule)"/><rect x="0" y="7" width="70" height="2" fill="var(--rule)"/><circle cx="90" cy="6" r="4" fill="var(--green)"/><rect x="110" y="2" width="70" height="2" fill="var(--rule)"/><rect x="110" y="7" width="70" height="2" fill="var(--rule)"/></svg>
  <div class="tile" style="left:60px;top:152px;width:391px;height:333px;background:linear-gradient(135deg,#e8e4da,#d6c48e 45%,#9a8566 80%,#6b5a45)" role="img" aria-label="Cluster of lit white pillar candles on wooden stands"></div>
  <div class="tile" style="left:459px;top:152px;width:408px;height:158px;background:linear-gradient(180deg,#9a9a92,#e6e4de 55%,#6f7a5c)" role="img" aria-label="White pillar candles in a floral table arrangement">
    <div class="tile-overlay"><span class="zoom"><svg width="18" height="18" viewBox="0 0 18 18"><circle cx="7.5" cy="7.5" r="5" stroke="#c0282d" stroke-width="2.5" fill="none"/><path d="M11 11l5 5" stroke="#c0282d" stroke-width="3"/></svg></span>Lorem Ipsum is simply dummy text</div>
  </div>
  <div class="tile" style="left:459px;top:320px;width:201px;height:165px;background:linear-gradient(135deg,#5a5a58,#d8d6d0 50%,#8a8882)" role="img" aria-label="White pillar candles of varied heights being lit"></div>
  <div class="tile" style="left:668px;top:320px;width:199px;height:165px;background:linear-gradient(90deg,#0a0a0a,#ebe9e4 30%,#111 50%,#ebe9e4 70%,#0a0a0a)" role="img" aria-label="Tall white taper and pillar candles on black"></div>
  <div class="tile" style="left:875px;top:152px;width:265px;height:333px;background:linear-gradient(180deg,#e9ece4,#93b06a 30%,#f2efe6 55%,#55703a)" role="img" aria-label="Large white pillar candle centrepiece in a ring of cream roses"></div>
</section>

<section class="testimonial">
  <h2 class="section-title">Client <em>Testimonial</em></h2>
  <svg class="title-rule" width="240" height="12" viewBox="0 0 240 12"><rect x="0" y="2" width="100" height="2" fill="var(--rule)"/><rect x="0" y="7" width="100" height="2" fill="var(--rule)"/><circle cx="120" cy="6" r="4" fill="var(--green)"/><rect x="140" y="2" width="100" height="2" fill="var(--rule)"/><rect x="140" y="7" width="100" height="2" fill="var(--rule)"/></svg>
  <div class="avatar" role="img" aria-label="Client portrait"></div>
  <p class="quote"><span class="mark">&ldquo;</span>Lorem ipsum dolor sit amet, consectetur adipiscing elit, sed do eiusmod tempor incididunt ut labore et dolore magna aliqua. Ut enim ad minim veniam, quis nostrud exercitation ullamco laboris nisi ut aliquip ex ea commodo consequat. Duis aute irure dolor in reprehenderit in voluptate velit esse cillum dolore eu fugiat nulla pariatur.</p>
  <div class="quote-rule"></div>
  <p class="author">- Miss Clara Wendell</p>
  <div class="dots"><i class="on"></i><i></i><i></i></div>
</section>

<footer class="site-footer">
  <div class="f-col" style="left:62px;width:190px">
    <h4>Quick Link</h4>
    <ul class="quick-links"><li>Home</li><li>About Us</li><li>Wedding</li><li>Corporate Event</li><li>For Hire</li><li>Contact</li></ul>
  </div>
  <div class="f-col" style="left:252px;width:300px;padding-left:59px">
    <h4>Contact Information</h4>
    <div class="contact-row" style="margin-top:18px"><svg width="20" height="24" viewBox="0 0 20 24"><path d="M10 1a7 7 0 0 0-7 7c0 5 7 12 7 12s7-7 7-12a7 7 0 0 0-7-7z" stroke="#fff" stroke-width="2" fill="none"/><circle cx="10" cy="8" r="2.5" fill="#fff"/><path d="M2 23h16" stroke="#fff" stroke-width="2"/></svg><span>48 Willow Lane<br>Harbour View<br>Northfield</span></div>
    <div class="contact-row big"><svg width="14" height="20" viewBox="0 0 14 20"><rect x="2" y="1" width="10" height="18" rx="2" stroke="#fff" stroke-width="2" fill="none"/><circle cx="7" cy="15.5" r="1.2" fill="#fff"/></svg>(123) 555-0182</div>
    <div class="contact-row"><svg width="14" height="11" viewBox="0 0 24 18" style="margin-top:5px"><path fill="#fff" d="M0 0h24v2L12 10 0 2zM0 4l12 8 12-8v14H0z"/></svg>info@hirealantern.com</div>
  </div>
  <div class="f-col inquiry" style="left:552px;width:330px;padding-left:49px">
    <h4>Quick Inquiry</h4>
    <input placeholder="Name" style="margin-top:14px"><input placeholder="Email"><textarea placeholder="Message"></textarea>
    <button>Submit</button>
  </div>
  <div class="footer-brand"><span class="brand-dot"></span>Hire a Lantern</div>
</footer>

<div class="bottom-bar">
  <p class="copyright">Copyright © 2016 Hire A Lantern |&nbsp; All rights reserved.</p>
  <div class="social"><span>Follow us on</span><i role="img" aria-label="Social link 1"></i><i role="img" aria-label="Social link 2"></i><i role="img" aria-label="Social link 3"></i><i role="img" aria-label="Social link 4"></i></div>
</div>

</body>
</html>
```